One piece Trade show banner, 8' x 8' square

One piece banner for trade show
8' x 8' airborne geophysical company

Target Market(s)

Business

Industry/Entity Type

mineral exploration and science

Colors
0054AA
0677BA
7BADD7
CADEEF
E8F1F8
FFC000
F8CF3A
FAE287
FDF2CF
FEFAEE

Requirements
Must have
• Company logo (attached), slogan (Airborne Geophysics for Discovery). We are looking for a new banner, for a standard 8 x 8' square one-piece booth. I have attached some pictures, our logo, our old banner for reference, and two examples from unrelated companies from a tradeshow that we like. If its possible I'd like to change the color of the helicopter from green to dark grey. IE, keep the orange and white, just change green to dark grey. Looking for a simple, clean design with minimal text.
Nice to have
• I have attached examples of banners that we like (2xIMG), plus our old 3-piece banner r.
Should not have
• Green in the helicopter. Please change the color of the helicopter with green/orange/white to dark grey/orange/white. IE change the green to dark grey and leave the orange and white alone. I've attached lots of pictures but I don't expect them all to be used.

```html
<!DOCTYPE html>
<html lang="en">
<head>
<meta charset="utf-8">
<title>Summit AeroSurveys – Trade Show Banner</title>
<link href="https://fonts.googleapis.com/css2?family=Poppins:wght@400;600;800&family=Barlow+Semi+Condensed:wght@700;800&display=swap" rel="stylesheet">
<style>
  :root {
    --blue-deep: #17387f;
    --blue-mid: #2156a6;
    --blue-brand: #0054AA;
    --yellow: #FFC000;
    --yellow-soft: #F8CF3A;
    --white: #ffffff;
    --ink: #151515;
    --sky-top: #ffffff;
    --sky-haze: #e9e3e2;
    --rock-light: #b79a8c;
    --rock-mid: #7d5d50;
    --rock-dark: #4d3932;
  }
  * { box-sizing: border-box; margin: 0; padding: 0; }
  html, body { width: 1152px; height: 1200px; overflow: hidden; background: var(--white); }
  .banner {
    position: relative;
    width: 1152px;
    height: 1200px;
    background: var(--white);
    font-family: "Poppins", sans-serif;
    overflow: hidden;
  }
  .hero-photo {
    position: absolute;
    left: 0; top: 0;
    width: 1152px; height: 690px;
    background:
      linear-gradient(180deg, var(--sky-top) 0%, var(--sky-top) 22%, var(--sky-haze) 45%, var(--rock-light) 62%, var(--rock-mid) 80%, var(--rock-dark) 100%);
  }
  .brand {
    position: absolute;
    right: 80px; top: 44px;
    display: flex; align-items: center; gap: 12px;
    font-family: "Poppins", sans-serif;
    font-weight: 600;
    font-size: 40px;
    color: var(--ink);
    letter-spacing: 0.5px;
  }
  .brand-dot {
    width: 18px; height: 18px; border-radius: 50%;
    background: var(--yellow);
  }
  .headline {
    position: absolute;
    left: 40px; top: 300px;
    font-family: "Poppins", sans-serif;
    font-weight: 800;
    font-size: 206px;
    line-height: 1;
    color: var(--white);
    letter-spacing: -4px;
  }
  .slogan {
    position: absolute;
    left: 44px; top: 500px;
    width: 1020px;
    font-family: "Barlow Semi Condensed", sans-serif;
    font-weight: 800;
    font-size: 86px;
    line-height: 1;
    color: var(--white);
    text-align: center;
    letter-spacing: -0.5px;
  }
  .since-tag {
    position: absolute;
    left: 188px; top: 600px;
    width: 700px; height: 66px;
    background: var(--yellow);
    display: flex; align-items: center; justify-content: center;
    font-family: "Barlow Semi Condensed", sans-serif;
    font-weight: 800;
    font-size: 50px;
    color: var(--white);
  }
  .services {
    position: absolute;
    left: 50px; top: 690px;
    width: 1042px; height: 370px;
    display: flex;
  }
  .survey-photo {
    width: 320px; height: 100%;
    background: radial-gradient(ellipse at 40% 30%, #1f7ee0 0%, #1261c4 40%, #0b3d8c 100%);
  }
  .service-panel {
    position: relative;
    flex: 1;
    background: linear-gradient(90deg, var(--blue-deep), var(--blue-mid));
    color: var(--white);
    padding: 50px 0 0 62px;
  }
  .service-grid {
    display: grid;
    grid-template-columns: 290px 300px;
    row-gap: 34px;
  }
  .service h3 {
    font-family: "Barlow Semi Condensed", sans-serif;
    font-weight: 800;
    font-size: 29px;
    line-height: 1.05;
    color: var(--yellow);
    letter-spacing: 0.3px;
  }
  .service ul { list-style: none; }
  .service li {
    font-size: 21px;
    line-height: 1.25;
    padding-left: 14px;
    position: relative;
  }
  .service li::before {
    content: "•";
    position: absolute; left: 0; top: 0;
    font-size: 16px;
  }
  .tech-line {
    position: absolute;
    left: 66px; top: 300px;
    width: 560px;
    font-size: 20px;
    line-height: 1.2;
  }
  .web-address {
    position: absolute;
    left: 0; top: 1100px;
    width: 1092px;
    text-align: center;
    font-family: "Poppins", sans-serif;
    font-weight: 800;
    font-size: 36px;
    color: var(--blue-deep);
    padding-left: 40px;
  }
</style>
</head>
<body>
  <div class="banner">
    <div class="hero-photo" role="img" aria-label="Photo of a dark grey and yellow survey helicopter with a long sensor boom flying over rugged mountain cliffs and clouds"></div>

    <div class="brand"><span class="brand-dot"></span>Summit AeroSurveys</div>

    <h1 class="headline">AIRBORNE</h1>
    <p class="slogan">GEOPHYSICS FOR DISCOVERY</p>
    <div class="since-tag">EXPLORING NEVADA SINCE 2007</div>

    <section class="services">
      <div class="survey-photo" role="img" aria-label="Photo of a helicopter towing an electromagnetic loop sensor over deep blue sky"></div>
      <div class="service-panel">
        <div class="service-grid">
          <div class="service">
            <h3>ELECTROMAGNETICS</h3>
            <ul>
              <li>Frequency domain</li>
              <li>Time domain</li>
              <li>Passive</li>
            </ul>
          </div>
          <div class="service">
            <h3>MAGNETICS</h3>
            <ul>
              <li>Helicopter, fixed wing, and drone</li>
              <li>Total field &amp; gradient</li>
            </ul>
          </div>
          <div class="service">
            <h3>RADIOMETRICS</h3>
            <ul>
              <li>256/512 channels</li>
              <li>Up to 33 litres</li>
            </ul>
          </div>
          <div class="service">
            <h3>CONSULTING</h3>
            <ul>
              <li>Survey design</li>
              <li>Interpretations</li>
              <li>Inversions</li>
            </ul>
          </div>
        </div>
        <p class="tech-line">TECHNOLOGIES Time Domain EMVLF-EM Magnetics Radiometrics</p>
      </div>
    </section>

    <p class="web-address">WWW.SUMMITAEROSURVEYS.COM</p>
  </div>
</body>
</html>
```